Thistlewick Superfoods Packaging Design

We are looking for a design for our premium superfoods powders and blends. Packaging dimensions are 21cm x 13cm Kraft packaging (light brown background). This design should be a blueprint for other products that we will be marketing including lions mane mushroom, reishi mushroom, Chaga mushroom, Spirilina, bee pollen, açai powder and the like. The design should be clean but earthy, and the template replicable for other products.

```html
<!DOCTYPE html>
<html lang="en">
<head>
<meta charset="utf-8">
<title>Thistlewick Superfoods – Moringa Leaf Pouch</title>
<link href="https://fonts.googleapis.com/css2?family=Montserrat:wght@500;600;700;800;900&display=swap" rel="stylesheet">
<style>
  :root{
    --bg:#e9efe9;
    --forest:#1d4f17;
    --forest-deep:#163f12;
    --lime:#7bb12a;
    --silver:#e6e7e6;
    --ink:#1a1a1a;
    --white:#ffffff;
  }
  html,body{margin:0;padding:0;width:1200px;height:1200px;overflow:hidden;background:var(--bg);}
  .canvas{position:relative;width:1200px;height:1200px;}
  .pouch{
    position:absolute;left:240px;top:37px;width:620px;height:970px;
    transform:scale(1.1613);transform-origin:0 0;
    font-family:"Montserrat",sans-serif;overflow:hidden;background:var(--silver);
  }
  .pouch-art{position:absolute;inset:0;}
  .brand{position:absolute;left:0;right:0;top:200px;text-align:center;color:var(--ink);font-weight:600;}
  .brand-name{font-size:58px;letter-spacing:1px;line-height:1;display:inline-flex;align-items:center;gap:10px;}
  .brand-dot{width:16px;height:16px;border-radius:50%;background:var(--ink);display:inline-block;}
  .brand-rule{width:330px;height:2px;background:var(--ink);margin:22px auto 10px;}
  .brand-tag{font-size:19px;letter-spacing:4px;}
  .product-title{position:absolute;left:0;right:0;top:372px;text-align:center;color:var(--forest);
    font-weight:900;font-size:88px;line-height:80px;letter-spacing:-1px;margin:0;}
  .intro{position:absolute;left:70px;right:70px;top:546px;text-align:center;margin:0;
    font-weight:800;font-size:12px;line-height:16px;color:var(--ink);text-transform:uppercase;}
  .facts{position:absolute;left:38px;top:622px;width:544px;height:178px;}
  .facts-bg{position:absolute;inset:0;}
  .fact-list{position:absolute;left:36px;top:14px;margin:0;padding:0;list-style:none;}
  .fact-list li{display:flex;align-items:center;gap:10px;color:var(--white);font-weight:700;
    font-size:12px;line-height:15px;text-transform:uppercase;height:39px;}
  .fact-list svg{width:29px;height:29px;flex:none;}
  .fact-body{position:absolute;left:300px;top:16px;width:232px;margin:0;color:var(--white);
    font-weight:500;font-size:10.4px;line-height:13.2px;text-align:center;}
  .leaf-art{position:absolute;left:172px;top:752px;width:160px;height:150px;border-radius:50% 50% 45% 55%;
    background:radial-gradient(circle at 45% 40%,#5a9a34,#2f6a1e);}
  .leaf-stem{position:absolute;left:246px;top:890px;width:8px;height:80px;background:#4f8c2c;border-radius:4px;}
  .badges{position:absolute;left:0;top:0;width:620px;height:970px;pointer-events:none;}
  .weight{position:absolute;left:398px;top:813px;width:40px;height:40px;border-radius:50%;
    border:2px solid #555;box-sizing:border-box;display:flex;align-items:center;justify-content:center;
    font-size:11px;font-weight:600;color:var(--ink);background:var(--white);}
</style>
</head>
<body>
<div class="canvas">
  <div class="pouch">
    <svg class="pouch-art" viewBox="0 0 620 970" width="620" height="970" aria-hidden="true">
      <rect width="620" height="970" fill="var(--forest)"/>
      <path d="M0 48 C150 50 380 90 620 160 L620 205 C400 120 180 72 0 66 Z" fill="var(--lime)"/>
      <path d="M0 66 C180 72 400 120 620 205 L620 905 C450 915 300 880 0 838 Z" fill="var(--silver)"/>
      <path d="M0 838 C300 880 450 915 620 905 L620 925 C450 935 300 905 0 860 Z" fill="var(--lime)" opacity="0"/>
      <path d="M390 922 C470 918 560 912 620 905 L620 925 C560 930 470 930 390 922 Z" fill="var(--lime)"/>
    </svg>

    <div class="brand">
      <div class="brand-name"><span class="brand-dot"></span>Thistlewick</div>
      <div class="brand-rule"></div>
      <div class="brand-tag">SUPERFOODS</div>
    </div>

    <h1 class="product-title">MORINGA<br>LEAF</h1>

    <p class="intro">Moringa, also known as ‘the miracle tree’, has been praised for it’s health benefits for thousands of years. It is extremely rich in healthy antioxidants and bioactive compounds. If fact it has:</p>

    <section class="facts">
      <svg class="facts-bg" viewBox="0 0 544 178" width="544" height="178" aria-hidden="true">
        <rect width="544" height="178" fill="var(--forest-deep)"/>
        <path d="M248 0 L290 0 C280 40 272 90 268 178 L262 178 C262 110 250 50 222 0 Z" fill="var(--silver)"/>
      </svg>
      <ul class="fact-list">
        <li><svg viewBox="0 0 30 30"><circle cx="14" cy="15" r="11" fill="none" stroke="#fff" stroke-width="2.5"/><path d="M8 15 L13 20 L27 5" fill="none" stroke="#fff" stroke-width="3"/></svg><span>7x the vitamin C<br>of oranges</span></li>
        <li><svg viewBox="0 0 30 30"><circle cx="14" cy="15" r="11" fill="none" stroke="#fff" stroke-width="2.5"/><path d="M8 15 L13 20 L27 5" fill="none" stroke="#fff" stroke-width="3"/></svg><span>3x the potassium<br>of bananas</span></li>
        <li><svg viewBox="0 0 30 30"><circle cx="14" cy="15" r="11" fill="none" stroke="#fff" stroke-width="2.5"/><path d="M8 15 L13 20 L27 5" fill="none" stroke="#fff" stroke-width="3"/></svg><span>4x the calcium<br>of milk</span></li>
        <li><svg viewBox="0 0 30 30"><circle cx="14" cy="15" r="11" fill="none" stroke="#fff" stroke-width="2.5"/><path d="M8 15 L13 20 L27 5" fill="none" stroke="#fff" stroke-width="3"/></svg><span>3x iron of<br>spinich</span></li>
      </ul>
      <p class="fact-body">The Leaves Contain All Nine Essential Amino Acids And Traditionally Used In Assisting The Healing Of Many Ailments. The Nutiritional Diveristy Is Also Known To Reduce Both Cholesterol And Blood Sugar Levels Whilst And Have Serious Anti-inflammatory Benefits. Our 100% Organic Moringa Is Grown And Harvested In It’s Native Envionment, Supporting Premium Superfood Nutrition.</p>
    </section>

    <div class="leaf-stem" aria-hidden="true"></div>
    <div class="leaf-art" role="img" aria-label="Illustration of a sprig of fresh moringa leaves"></div>

    <div class="weight">250g</div>
    <svg class="badges" viewBox="0 0 620 970" width="620" height="970" aria-hidden="true">
      <circle cx="470" cy="833" r="21" fill="#fff" stroke="#555" stroke-width="2"/>
      <circle cx="390" cy="880" r="21" fill="#2c4a2a"/>
      <circle cx="440" cy="880" r="20" fill="#fff" stroke="var(--lime)" stroke-width="3"/>
      <rect x="470" y="862" width="54" height="36" rx="3" fill="#fff" stroke="var(--lime)" stroke-width="3"/>
    </svg>
  </div>
</div>
</body>
</html>
```